Health Care Company with Logo Needs Business Cards designed

We are a luxury behavioral health company looking for business cards design we already have a logo and are looking for someone to design a sophisticated luxurious looking business card. Please note that Card design should be captivating just like the logo and also encompass the logo color

Industry/Entity Type

Healthcare

Contact Information for Business Card

Logo,company name, tagline, my name and title, contact details, and physical address

```html
<!DOCTYPE html>
<html lang="en">
<head>
<meta charset="utf-8">
<title>Arden Behavioral Health – Business Cards</title>
<link href="https://fonts.googleapis.com/css2?family=Roboto:wght@400;500;700&display=swap" rel="stylesheet">
<style>
  :root {
    --bg: #e9e9e7;
    --card: #ffffff;
    --purple: #6a2c8e;
    --blue: #12a3e0;
    --orange: #ef8a1c;
    --green: #7ab833;
    --ink: #4a4a4a;
    --muted: #777777;
    --line: #555555;
  }
  * { box-sizing: border-box; margin: 0; padding: 0; }
  html, body { width: 1200px; height: 802px; overflow: hidden; }
  body {
    background: var(--bg);
    font-family: "Roboto", Arial, sans-serif;
    color: var(--ink);
    position: relative;
  }
  .card {
    position: absolute;
    top: 251px;
    width: 525px;
    height: 300px;
    background: var(--card);
    box-shadow: 0 6px 18px rgba(0,0,0,0.12);
    overflow: hidden;
  }
  .card--front { left: 60px; }
  .card--back { left: 615px; }

  /* Company name block */
  .brand { position: absolute; display: flex; align-items: center; gap: 10px; }
  .brand__mark { width: 30px; height: 30px; background: var(--purple); flex: none; }
  .brand__name {
    font-weight: 700;
    color: var(--purple);
    font-size: 23px;
    line-height: 1;
    white-space: nowrap;
  }
  .brand__tagline {
    display: block;
    margin-top: 5px;
    font-weight: 400;
    font-size: 10px;
    color: var(--muted);
  }
  .card--front .brand { left: 44px; top: 42px; }

  /* Front: person and contacts */
  .person { position: absolute; left: 44px; top: 126px; width: 190px; text-align: right; }
  .person__name { font-size: 24px; font-weight: 700; color: var(--blue); line-height: 1.1; }
  .person__title { font-size: 16px; color: var(--ink); margin-top: 5px; }
  .divider { position: absolute; left: 252px; top: 116px; width: 1px; height: 76px; background: #bdbdbd; }
  .contacts { position: absolute; left: 268px; top: 120px; list-style: none; }
  .contacts li { display: flex; align-items: center; gap: 9px; font-size: 15px; line-height: 24px; color: var(--ink); }
  .contacts svg { width: 13px; height: 13px; flex: none; }

  /* Front: bottom band */
  .band { position: absolute; left: 0; right: 0; bottom: 0; height: 64px; background: var(--purple); }
  .band__stripe { position: absolute; left: 0; right: 0; top: 0; height: 8px; display: flex; }
  .band__stripe span { height: 100%; }
  .band__address {
    position: absolute; left: 0; right: 0; top: 16px;
    text-align: center; color: #fff; font-size: 15px; letter-spacing: 0.3px;
  }
  .band__rule { position: absolute; left: 0; right: 0; bottom: 12px; height: 3px; background: #fff; }

  /* Back: appointment form */
  .card--back .brand { right: 30px; top: 30px; }
  .card--back .brand__mark { width: 26px; height: 26px; }
  .card--back .brand__name { font-size: 20px; }
  .card--back .brand__tagline { font-size: 9px; }
  .form__title {
    position: absolute; left: 34px; top: 38px;
    font-size: 18px; font-weight: 700; color: var(--blue); letter-spacing: 0.5px;
  }
  .field { position: absolute; display: flex; align-items: flex-end; gap: 8px; font-size: 15px; color: var(--ink); }
  .field__rule { flex: 1; height: 1px; background: var(--line); margin-bottom: 3px; }
  .field--name { left: 34px; right: 30px; top: 92px; }
  .field--date { left: 34px; width: 200px; top: 130px; }
  .field--time { left: 250px; width: 140px; top: 130px; }
  .checks { position: absolute; display: flex; gap: 16px; font-size: 15px; color: var(--ink); }
  .checks label { display: flex; align-items: center; gap: 7px; }
  .box { width: 14px; height: 14px; border: 2px solid var(--blue); display: inline-block; }
  .checks--ampm { left: 408px; top: 132px; }
  .checks--days { left: 34px; top: 172px; }
  .blank { position: absolute; left: 34px; right: 30px; height: 1px; background: var(--line); }
  .blank--1 { top: 228px; }
  .blank--2 { top: 262px; }
</style>
</head>
<body>

<section class="card card--front" aria-label="Business card front">
  <div class="brand">
    <span class="brand__mark"></span>
    <div>
      <div class="brand__name">Arden Behavioral Health</div>
      <span class="brand__tagline">Compassionate care for every step</span>
    </div>
  </div>

  <div class="person">
    <div class="person__name">Daniel Moore</div>
    <div class="person__title">Manager</div>
  </div>
  <div class="divider"></div>
  <ul class="contacts">
    <li>
      <svg viewBox="0 0 24 24" aria-hidden="true"><path fill="#12a3e0" d="M6.6 10.8a15.1 15.1 0 0 0 6.6 6.6l2.2-2.2c.3-.3.7-.4 1-.2 1.1.4 2.3.6 3.6.6.6 0 1 .4 1 1V20c0 .6-.4 1-1 1A17 17 0 0 1 3 4c0-.6.4-1 1-1h3.5c.6 0 1 .4 1 1 0 1.3.2 2.5.6 3.6.1.3 0 .7-.2 1z"/></svg>
      555-014-2100
    </li>
    <li>
      <svg viewBox="0 0 24 24" aria-hidden="true"><rect x="2.5" y="5" width="19" height="14" fill="none" stroke="#12a3e0" stroke-width="2"/><path d="M3 6l9 7 9-7" fill="none" stroke="#12a3e0" stroke-width="2"/></svg>
      hello@ardenhealth.com
    </li>
    <li>
      <svg viewBox="0 0 24 24" aria-hidden="true"><circle cx="12" cy="12" r="9.5" fill="none" stroke="#12a3e0" stroke-width="2"/><ellipse cx="12" cy="12" rx="4" ry="9.5" fill="none" stroke="#12a3e0" stroke-width="1.6"/><path d="M2.5 12h19M4 7h16M4 17h16" stroke="#12a3e0" stroke-width="1.4"/></svg>
      www.ardenhealth.com
    </li>
  </ul>

  <div class="band">
    <div class="band__stripe">
      <span style="width:30px;background:var(--purple)"></span>
      <span style="width:140px;background:var(--blue)"></span>
      <span style="width:12px;background:var(--purple)"></span>
      <span style="width:130px;background:var(--orange)"></span>
      <span style="width:12px;background:var(--purple)"></span>
      <span style="width:130px;background:var(--green)"></span>
      <span style="flex:1;background:var(--purple)"></span>
    </div>
    <div class="band__address">Your address, city, state, ZIP 0000</div>
    <div class="band__rule"></div>
  </div>
</section>

<section class="card card--back" aria-label="Business card back, appointment reminder">
  <div class="form__title">APPOINTMENT</div>
  <div class="brand">
    <span class="brand__mark"></span>
    <div>
      <div class="brand__name">Arden Behavioral Health</div>
      <span class="brand__tagline">Compassionate care for every step</span>
    </div>
  </div>

  <div class="field field--name">NAME <span class="field__rule"></span></div>
  <div class="field field--date">DATE <span class="field__rule"></span></div>
  <div class="field field--time">TIME <span class="field__rule"></span></div>

  <div class="checks checks--ampm">
    <label><span class="box"></span>AM</label>
    <label><span class="box"></span>PM</label>
  </div>

  <div class="checks checks--days">
    <label><span class="box"></span>MON</label>
    <label><span class="box"></span>TUE</label>
    <label><span class="box"></span>WED</label>
    <label><span class="box"></span>THU</label>
    <label><span class="box"></span>FRI</label>
    <label><span class="box"></span>SAT</label>
  </div>

  <div class="blank blank--1"></div>
  <div class="blank blank--2"></div>
</section>

</body>
</html>
```